Kestrel Facilities Business Card Design

We would now like to design business cards with the new Kestrel Facilities logo

Target Market(s)

Professional

Industry/Entity Type

Professional services

Contact Information for Business Card

Employee name, title, phone number, email address, corporate office address and logo.

Font styles to use
Sans Serif

Colors
0054AA
0677BA
7BADD7
CADEEF
E8F1F8

Requirements
Must have
• My logo
Should not have
• any other pictures or images besides my logo

```html
<!DOCTYPE html>
<html lang="en">
<head>
<meta charset="utf-8">
<title>Kestrel Facilities Business Card</title>
<link href="https://fonts.googleapis.com/css2?family=Montserrat:wght@400;500;700;800&display=swap" rel="stylesheet">
<style>
  :root {
    --brand-blue: #3276BE;
    --line-blue: #2F6DB5;
    --soft-grey: #A9A9AB;
    --logo-silver: #C9CFDE;
    --paper: #FFFFFF;
    --ink: #1E1E1E;
    --backdrop: #2B2B2B;
  }
  * { margin: 0; padding: 0; box-sizing: border-box; }
  html, body { width: 1200px; height: 960px; overflow: hidden; }
  body {
    background: var(--backdrop);
    font-family: "Montserrat", sans-serif;
    position: relative;
  }
  .card {
    position: absolute;
    width: 560px;
    height: 320px;
    border-radius: 18px;
    overflow: hidden;
    box-shadow: 0 14px 30px rgba(0,0,0,0.45);
  }
  .card-back {
    left: 70px;
    top: 110px;
    background: var(--brand-blue);
    display: flex;
    align-items: center;
    justify-content: center;
  }
  .wordmark {
    display: flex;
    align-items: center;
    gap: 14px;
    font-weight: 700;
    letter-spacing: 0.5px;
    line-height: 1.05;
  }
  .wordmark-mark {
    width: 22px;
    height: 22px;
    flex: none;
  }
  .card-back .wordmark { color: var(--logo-silver); font-size: 40px; }
  .card-back .wordmark-mark { background: var(--logo-silver); width: 28px; height: 28px; }

  .card-front {
    left: 570px;
    top: 470px;
    background: var(--paper);
  }
  .wave { position: absolute; inset: 0; width: 560px; height: 320px; }
  .card-front .wordmark {
    position: absolute;
    left: 36px;
    top: 88px;
    color: var(--brand-blue);
    font-size: 28px;
    width: 230px;
  }
  .card-front .wordmark-mark { background: var(--brand-blue); }
  .divider {
    position: absolute;
    left: 282px;
    top: 36px;
    width: 2px;
    height: 150px;
    background: var(--line-blue);
  }
  .contact {
    position: absolute;
    left: 304px;
    top: 30px;
    color: var(--ink);
  }
  .person-name {
    color: var(--brand-blue);
    font-weight: 800;
    font-size: 19px;
    letter-spacing: 0.3px;
  }
  .person-title { font-size: 13px; font-weight: 500; margin-top: 2px; }
  .address { font-size: 12px; margin-top: 12px; line-height: 1.4; }
  .channels { list-style: none; margin-top: 10px; font-size: 12px; line-height: 1.55; }
  .channels li { display: flex; align-items: center; gap: 7px; }
  .channels svg { width: 12px; height: 12px; flex: none; fill: var(--brand-blue); }
</style>
</head>
<body>

<section class="card card-back" aria-label="Business card back">
  <div class="wordmark"><span class="wordmark-mark"></span><span>Kestrel<br>Facilities</span></div>
</section>

<section class="card card-front" aria-label="Business card front">
  <svg class="wave" viewBox="0 0 560 320" aria-hidden="true">
    <path d="M0,320 L0,292 C50,222 170,238 310,224 C440,212 532,204 548,112 L560,112 L560,320 Z" fill="var(--soft-grey)"/>
    <path d="M0,320 L0,306 C55,236 175,252 315,238 C445,226 545,220 560,124 L560,320 Z" fill="var(--brand-blue)"/>
  </svg>

  <div class="wordmark"><span class="wordmark-mark"></span><span>Kestrel<br>Facilities</span></div>

  <div class="divider"></div>

  <div class="contact">
    <h1 class="person-name">DARIN HOLLOWAY</h1>
    <p class="person-title">Co-Founder</p>
    <p class="address">1840 N. Harbor Lane<br>Suite 402 Westfield 17</p>
    <ul class="channels">
      <li><svg viewBox="0 0 24 24"><path d="M6.6 10.8a15 15 0 0 0 6.6 6.6l2.2-2.2c.3-.3.7-.4 1-.2 1.1.4 2.3.6 3.6.6.6 0 1 .4 1 1V20c0 .6-.4 1-1 1C10.6 21 3 13.4 3 4c0-.6.4-1 1-1h3.5c.6 0 1 .4 1 1 0 1.3.2 2.5.6 3.6.1.3 0 .7-.2 1z"/></svg>+254-300-41722</li>
      <li><svg viewBox="0 0 24 24"><path d="M2 5h20v14H2z M3 6l9 7 9-7" fill="none" stroke="var(--brand-blue)" stroke-width="2.4"/></svg>info@kestrelfm.com</li>
      <li><svg viewBox="0 0 24 24"><circle cx="12" cy="12" r="10"/></svg>www.kestrelfm.com</li>
    </ul>
  </div>
</section>

</body>
</html>
```